Brightfen Business Card Redesign & Logo Update

We need to update our business cards to something more modern and fresh. Brightfen can provide the current color schemes and old design examples, but welcome creativity in helping us with this redesign. PLEASE NOTE that we no longer utilize the "tree" and/or "leaf" imagery in our branding. If able would apprecaite an update on the quality of our "words only" logo in Ai. / PNG formats too.

Target Market(s)

Investors, landowners, corporate partners, contractors

Industry/Entity Type

Environmental Restoration & Conservation

Contact Information for Business Card

Logo, persons name, title, mailing address, phone and email, website url

Font styles to use
Other font styles liked:
• Merriweather

Requirements
Nice to have
• Logo, persons name, title, mailing address, phone and email, website url, but open to ideams
Should not have
• No all back backgrounds

```html
<!DOCTYPE html>
<html lang="en">
<head>
<meta charset="UTF-8">
<title>Brightfen Business Card</title>
<link rel="stylesheet" href="https://fonts.googleapis.com/css2?family=Montserrat:wght@400;500;700&display=swap">
<style>
  :root {
    --stage: #3a3a3a;
    --card: #1f1f1f;
    --orange: #f08221;
    --green: #138040;
    --white: #ffffff;
    --soft: #e9e9e9;
  }
  * { margin: 0; padding: 0; box-sizing: border-box; }
  html, body {
    width: 1200px; height: 900px; overflow: hidden;
    background: var(--stage);
    font-family: "Montserrat", Arial, sans-serif;
  }
  .card {
    position: absolute; left: 100px; top: 165px;
    width: 1000px; height: 570px;
    background: var(--card);
    box-shadow: 0 20px 50px rgba(0,0,0,.45);
    overflow: hidden;
  }
  .brand {
    position: absolute; left: 150px; top: 185px;
  }
  .brand-name {
    font-weight: 700; font-size: 64px; letter-spacing: 2px;
    color: var(--orange); line-height: 1; text-transform: uppercase;
  }
  .brand-descriptor {
    margin-top: 10px;
    font-weight: 500; font-size: 17px; letter-spacing: 1.5px;
    color: var(--white); text-transform: uppercase;
  }
  .divider {
    position: absolute; left: 598px; top: 130px;
    width: 1px; height: 300px; background: var(--green);
  }
  .contact {
    position: absolute; left: 640px; top: 150px;
    color: var(--soft);
  }
  .person-name {
    font-weight: 700; font-size: 30px; letter-spacing: 2px;
    text-transform: uppercase; line-height: 1.1;
  }
  .person-name .first { color: var(--green); }
  .person-name .last { color: var(--orange); }
  .person-title { font-size: 20px; margin-top: 4px; }
  .address { font-size: 20px; line-height: 1.35; margin-top: 22px; }
  .lines { list-style: none; margin-top: 18px; font-size: 20px; line-height: 1.6; }
  .lines li { display: flex; align-items: center; gap: 10px; }
  .lines svg { width: 16px; height: 16px; fill: var(--orange); flex: none; }
  .band {
    position: absolute; left: 0; bottom: 0; width: 1000px; height: 16px;
  }
</style>
</head>
<body>
  <div class="card">
    <div class="brand">
      <div class="brand-name">Brightfen</div>
      <div class="brand-descriptor">Environmental Credit Company</div>
    </div>

    <div class="divider"></div>

    <div class="contact">
      <div class="person-name"><span class="first">Mark</span> <span class="last">Ellison</span></div>
      <div class="person-title">CEO/Founder</div>
      <div class="address">48 Alder Mill Road<br>Fenwick, ON 20817</div>
      <ul class="lines">
        <li>
          <svg viewBox="0 0 16 16" aria-hidden="true"><path d="M3.6 1.2l2.3 2.8-1.3 1.6c.9 2 2.5 3.6 4.6 4.6l1.6-1.3 2.8 2.3-1.4 2.3C7 13.1 2.9 9 1.5 3.1z"/></svg>
          (555) 318 2046
        </li>
        <li>
          <svg viewBox="0 0 16 16" aria-hidden="true"><path d="M1 3h14v10H1z M2.2 4.2L8 8.6l5.8-4.4z" fill-rule="evenodd"/></svg>
          Mark@brightfen.com
        </li>
        <li>
          <svg viewBox="0 0 16 16" aria-hidden="true"><path d="M8 1a7 7 0 100 14A7 7 0 008 1zm0 1.6c.8 1 1.3 2.6 1.5 4.6h-3C6.7 5.2 7.2 3.6 8 2.6zM2.6 8.8h2.3c.1 1.7.5 3.2 1.1 4.3a5.5 5.5 0 01-3.4-4.3zm0-1.6a5.5 5.5 0 013.4-4.3c-.6 1.1-1 2.6-1.1 4.3zm3.9 1.6h3c-.2 2-.7 3.6-1.5 4.6-.8-1-1.3-2.6-1.5-4.6zm3.5 4.3c.6-1.1 1-2.6 1.1-4.3h2.3a5.5 5.5 0 01-3.4 4.3zm1.1-5.9c-.1-1.7-.5-3.2-1.1-4.3a5.5 5.5 0 013.4 4.3z"/></svg>
          www.brightfen.com
        </li>
      </ul>
    </div>

    <svg class="band" viewBox="0 0 1000 16" preserveAspectRatio="none" aria-hidden="true">
      <polygon points="0,0 475,0 460,16 0,16" fill="var(--orange)"/>
      <polygon points="475,0 1000,0 1000,16 460,16" fill="var(--green)"/>
    </svg>
  </div>
</body>
</html>
```